Business Card for a Dental Office

The design should communicate integrity, quality and reliability. We also want the card look elegant, simple, but still stand out, different from the traditional-dental-office business card.

Industry/Entity Type

Business

```html
<!DOCTYPE html>
<html lang="en">
<head>
<meta charset="utf-8">
<title>Dental Office Business Cards</title>
<link href="https://fonts.googleapis.com/css2?family=Open+Sans:wght@400;600;700&display=swap" rel="stylesheet">
<style>
  :root {
    --page-bg: #ecebe8;
    --card-black: #000000;
    --yellow-light: #f0e21a;
    --yellow-mid: #e6d61d;
    --yellow-dark: #d4bf24;
    --ink: #1b1b1b;
    --paper: #ffffff;
  }
  * { box-sizing: border-box; margin: 0; padding: 0; }
  html, body { width: 1200px; height: 900px; overflow: hidden; }
  body {
    background: var(--page-bg);
    font-family: "Open Sans", Arial, sans-serif;
    color: var(--ink);
    position: relative;
  }

  /* Front card */
  .card-front {
    position: absolute; left: 238px; top: 62px;
    width: 555px; height: 342px;
    background: var(--card-black);
    overflow: hidden;
    box-shadow: 0 4px 14px rgba(0,0,0,.18);
  }
  .card-front .roof { position: absolute; inset: 0; }
  .front-text {
    position: absolute; left: 0; right: 0; top: 124px;
    text-align: center;
  }
  .person-name { font-size: 21px; font-weight: 700; line-height: 28px; }
  .person-title { font-size: 15px; line-height: 22px; margin-bottom: 14px; }
  .contact-line {
    display: flex; justify-content: center; align-items: center; gap: 6px;
    font-size: 14.5px; line-height: 20.3px;
  }
  .contact-line svg { width: 11px; height: 11px; fill: var(--ink); }
  .address { position: absolute; left: 0; right: 0; top: 306px; text-align: center; font-size: 14.5px; }

  /* Back card */
  .card-back {
    position: absolute; left: 458px; top: 518px;
    width: 559px; height: 343px;
    background: var(--paper);
    box-shadow: 0 4px 14px rgba(0,0,0,.18);
  }
  .brand { position: absolute; left: 68px; top: 66px; display: flex; align-items: center; gap: 14px; }
  .brand-mark { width: 48px; height: 48px; background: var(--ink); flex: none; }
  .brand-name { font-size: 25px; font-weight: 700; letter-spacing: .3px; line-height: 30px; color: var(--ink); }
  .brand-tagline { font-size: 13.5px; font-weight: 400; color: var(--ink); text-transform: uppercase; letter-spacing: .4px; line-height: 18px; }
  .appointment-title {
    position: absolute; left: 0; right: 0; top: 130px;
    text-align: center; font-size: 22.5px;
  }
  .field {
    position: absolute; left: 73px; display: flex; align-items: baseline;
    font-size: 15.5px;
  }
  .field .fill { border-bottom: 1.5px dotted var(--ink); height: 12px; margin-left: 8px; }
  .field .unit { margin: 0 10px; }
  .field-name { top: 174px; }
  .field-date { top: 219px; }
  .field-time { top: 259px; }
  .notice { position: absolute; left: 0; right: 0; top: 297px; text-align: center; font-size: 16px; }
</style>
</head>
<body>

<section class="card-front">
  <svg class="roof" viewBox="0 0 555 342" aria-hidden="true">
    <polygon points="284,0 0,222 0,342 555,342 555,214" fill="var(--yellow-mid)"/>
    <polygon points="284,48 52,222 519,214" fill="var(--yellow-dark)"/>
    <polygon points="0,222 555,214 555,342 0,342" fill="var(--yellow-light)" opacity=".55"/>
  </svg>
  <div class="front-text">
    <p class="person-name">Jonathan Smith</p>
    <p class="person-title">Managing Director</p>
    <p class="contact-line"><svg viewBox="0 0 12 12"><rect x="3" y="0" width="6" height="12" rx="1"/></svg>123-456-7890</p>
    <p class="contact-line"><svg viewBox="0 0 12 12"><path d="M0 4q6-5 12 0v2h-3v-2h-6v2h-3z M2 7h8v5h-8z"/></svg>123-456-7890</p>
    <p class="contact-line"><svg viewBox="0 0 12 12"><rect x="0" y="4" width="12" height="8" rx="1"/><rect x="3" y="0" width="6" height="4"/></svg>123-456-7890</p>
    <p class="contact-line"><svg viewBox="0 0 12 12"><path d="M0 2h12v8h-12z"/></svg>info@youremail.com</p>
    <p class="contact-line"><svg viewBox="0 0 12 12"><path d="M1 8l3-3 1.5 1.5-3 3zM6.5 5.5l3-3 1.5 1.5-3 3zM4 8l4-4 .8.8-4 4z"/></svg>www.yourweb.com</p>
  </div>
  <p class="address">1234, Address Goes Here Country Name, 123456</p>
</section>

<section class="card-back">
  <div class="brand">
    <span class="brand-mark"></span>
    <div>
      <p class="brand-name">HARWICK DENTAL CENTRE</p>
      <p class="brand-tagline">Gentle care for every family smile</p>
    </div>
  </div>
  <p class="appointment-title">Your Next Appointment is</p>
  <p class="field field-name">Name :<span class="fill" style="width:312px"></span></p>
  <p class="field field-date">Date :<span class="fill" style="width:320px"></span></p>
  <p class="field field-time">Time:<span class="fill" style="width:122px"></span><span class="unit">AM</span><span class="fill" style="width:136px;margin-left:0"></span><span class="unit">PM</span></p>
  <p class="notice">If unable to keep appointment,&nbsp; kindly give 24hrs notice.</p>
</section>

</body>
</html>
```